Veldmark Supplies Business Card

Professional business card that stand out to our potential customers. Front and back with clean modern design

Industry/Entity Type

Oil and gas

Contact Information for Business Card

Name, address, website , office phone and cell number

Requirements
Must have
• Editable files for each employee

```html
<!DOCTYPE html>
<html lang="en">
<head>
<meta charset="UTF-8">
<title>Veldmark Supplies Business Card</title>
<link href="https://fonts.googleapis.com/css2?family=Montserrat:wght@400;500;700;800&display=swap" rel="stylesheet">
<style>
  :root {
    --bg: #e9ebee;
    --cyan: #0aaecf;
    --cyan-deep: #078aa6;
    --red: #e8262b;
    --ink: #1b1b1b;
    --white: #ffffff;
  }
  * { box-sizing: border-box; margin: 0; padding: 0; }
  html, body {
    width: 1200px; height: 874px; overflow: hidden;
    background: var(--bg);
    font-family: "Montserrat", sans-serif;
  }
  .sheet {
    width: 1200px; height: 874px;
    display: flex; flex-direction: column;
    align-items: center; justify-content: center; gap: 30px;
  }
  .card {
    width: 700px; height: 400px;
    border-radius: 26px;
    position: relative;
    overflow: hidden;
    box-shadow: 0 10px 28px rgba(0,0,0,0.14);
  }
  /* Back */
  .card-back {
    background: var(--cyan);
    display: flex; align-items: center; justify-content: center;
  }
  .back-brand {
    display: flex; align-items: center; gap: 16px;
    color: var(--cyan-deep);
    font-weight: 800; font-size: 40px; letter-spacing: 1px;
    text-transform: uppercase;
  }
  .back-brand .brand-square {
    width: 34px; height: 34px; background: var(--cyan-deep);
  }
  /* Front */
  .card-front {
    background: var(--white);
    display: flex; align-items: center;
    padding: 0 44px 0 48px;
  }
  .front-brand {
    width: 300px;
    display: flex; flex-direction: column; align-items: flex-start; gap: 18px;
  }
  .front-brand .brand-square {
    width: 58px; height: 58px; background: var(--cyan);
  }
  .front-brand .brand-name {
    color: var(--red);
    font-weight: 800; font-size: 38px; line-height: 1.05;
    text-transform: uppercase; letter-spacing: 0.5px;
  }
  .details {
    margin-left: 24px;
    border-left: 2px solid var(--red);
    padding: 8px 0 8px 22px;
    color: var(--ink);
  }
  .person-name {
    color: var(--red); font-weight: 700; font-size: 26px; line-height: 1.1;
  }
  .person-title {
    font-size: 16px; font-weight: 500; margin: 4px 0 16px;
  }
  .contact-list { list-style: none; }
  .contact-list li {
    display: flex; align-items: center; gap: 10px;
    font-size: 15px; line-height: 1.65;
  }
  .contact-list svg { width: 14px; height: 14px; flex: none; fill: var(--red); }
  .address { font-size: 15px; line-height: 1.45; margin-top: 10px; }
</style>
</head>
<body>
<main class="sheet">
  <section class="card card-back" aria-label="Card back">
    <div class="back-brand">
      <span class="brand-square"></span>
      <span class="brand-name">Veldmark Supplies</span>
    </div>
  </section>

  <section class="card card-front" aria-label="Card front">
    <div class="front-brand">
      <span class="brand-square"></span>
      <span class="brand-name">Veldmark Supplies</span>
    </div>
    <div class="details">
      <h1 class="person-name">Daniel Harrow</h1>
      <p class="person-title">President</p>
      <ul class="contact-list">
        <li>
          <svg viewBox="0 0 24 24" aria-hidden="true"><path d="M4 9c0-3 4-5 8-5s8 2 8 5l-4 1-1-2H9L8 10 4 9zm2 3h12l1 8H5l1-8zm6 2a2.5 2.5 0 100 5 2.5 2.5 0 000-5z"/></svg>
          +1.555.014.0200 x123
        </li>
        <li>
          <svg viewBox="0 0 24 24" aria-hidden="true"><path d="M6.6 10.8a15 15 0 006.6 6.6l2.2-2.2a1 1 0 011-.25 11.4 11.4 0 003.6.6 1 1 0 011 1V20a1 1 0 01-1 1A17 17 0 013 4a1 1 0 011-1h3.5a1 1 0 011 1c0 1.25.2 2.45.6 3.6a1 1 0 01-.25 1z"/></svg>
          +1.555.201.4460
        </li>
        <li>
          <svg viewBox="0 0 24 24" aria-hidden="true"><path d="M2 5h20v14H2V5zm2 2v.5l8 5 8-5V7H4z"/></svg>
          info@veldmarksupplies.com
        </li>
        <li>
          <svg viewBox="0 0 24 24" aria-hidden="true"><path d="M12 2a10 10 0 100 20 10 10 0 000-20zm0 2c1 1.4 1.8 3.3 2 5H10c.2-1.7 1-3.6 2-5zM4.3 11h3.7c0 1.4.2 2.8.6 4H5.1a8 8 0 01-.8-4zm5.7 0h4c0 1.4-.3 2.8-.7 4h-2.6c-.4-1.2-.7-2.6-.7-4zm6 0h3.7a8 8 0 01-.8 4h-3.5c.4-1.2.6-2.6.6-4zM8.1 9H4.7a8 8 0 014.4-4.3A12 12 0 008.1 9zm7.8 0a12 12 0 00-1-4.3A8 8 0 0119.3 9h-3.4z"/></svg>
          www.veldmarksupplies.com
        </li>
      </ul>
      <p class="address">48 Ridgeline Avenue<br>Calder Falls, TX 79701 USA</p>
    </div>
  </section>
</main>
</body>
</html>
```